UX - Need some screens design for a Skill Assessment Application

I am building an app to carry out skill assessments. Depending on how the assessment is configured, it may have one or more parts
1. Question based assessment (Multiple Choice, True False, Fill in the blanks"
2. Endorsement by two colleagues - A screen that allows user to pick colleagues based on search and shows the status of pending requests
3. A written submission - a page that explains the format of the submission and a file upload
As each assessment can be configured with or without any of the steps, the assessment UI must be such that these areas get hidden/displayed based on configuration.
Colour codes to be used can be #0e78bb and #ffffff
There will also be a start screen (instructions) and an end screen (results)
Target Market(s)
Enterprise software
Number of Pages Required
4 page

```html
<!DOCTYPE html>
<html lang="en">
<head>
<meta charset="utf-8">
<title>Velvorn – Application Design Capabilities – Submission</title>
<link href="https://fonts.googleapis.com/css2?family=Inter:wght@400;500;600;700&family=Noto+Sans:wght@600&display=swap" rel="stylesheet">
<style>
:root{
  --brand:#0e78bb;
  --nav:#0055ad;
  --white:#ffffff;
  --ink:#1f2328;
  --text:#3b4048;
  --muted:#6b7078;
  --line:#d9dde3;
  --band:#f5f6f8;
  --pill:#e8eaed;
  --teal:#0f9a98;
  --drop-bg:#eaf5fb;
  --drop-line:#7ccbe6;
  --drop-icon:#a9dcef;
  --link:#1b86cf;
}
*{box-sizing:border-box;margin:0;padding:0}
html,body{width:1200px;height:771px;overflow:hidden;background:var(--white);font-family:'Inter',sans-serif;color:var(--ink)}
.canvas{position:relative;width:1200px;height:771px}
.abs{position:absolute}

.topbar{left:0;top:0;width:1200px;height:44px;background:var(--nav)}
.brand{left:70px;top:12px;display:flex;align-items:center;gap:10px;color:var(--white);font-size:14px;font-weight:600}
.brand-dot{width:18px;height:18px;border-radius:50%;background:var(--white)}
.nav-item{top:15px;font-size:12.5px;color:#cfe0f3}
.nav-item.active{color:var(--white);font-weight:700}
.nav-underline{left:487px;top:41px;width:80px;height:3px;background:#29a9e6}
.icon{top:12px}
.avatar{left:1099px;top:8px;width:28px;height:28px;border-radius:50%;background:linear-gradient(135deg,#8a6a7a,#3d3450)}

.crumbs{left:56px;top:66px;display:flex;align-items:center;gap:10px;font-size:11.5px;color:var(--muted)}
.crumbs a{color:var(--link);text-decoration:none;margin-left:2px}
.title{left:122px;top:96px;font-family:'Noto Sans',sans-serif;font-weight:600;font-size:22px;color:var(--ink)}
.updated{right:90px;top:111px;font-size:11px;color:var(--muted)}
.updated b{font-weight:400;color:var(--text)}

.band{left:0;top:140px;width:1200px;height:45px;background:var(--band);border-top:1px solid var(--line);border-bottom:1px solid var(--line)}
.meta{top:155px;font-size:10.5px;color:var(--ink)}
.meta .val{color:var(--link)}
.meta .plain{color:var(--muted)}
.sep{top:155px;width:1px;height:14px;background:var(--line)}
.pill{top:151px;height:24px;border-radius:12px;background:var(--pill);font-size:11px;color:var(--text);display:flex;align-items:center;justify-content:center}

.step{left:88px;width:214px;height:43px;border:1px solid var(--line);border-radius:4px;display:flex;align-items:center;justify-content:space-between;padding:0 16px;font-size:12px;color:var(--text)}
.step.current{border-color:var(--nav);color:var(--ink);font-weight:500}
.tick{width:14px;height:14px;border-radius:50%;background:var(--teal);display:flex;align-items:center;justify-content:center}

.section-title{left:366px;top:219px;font-size:16px;font-weight:600}
.btn-outline{border:1px solid var(--brand);border-radius:3px;color:var(--brand);font-size:11.5px;font-weight:500;display:flex;align-items:center;justify-content:center;background:var(--white)}
.rule{left:366px;top:254px;width:745px;height:1px;background:var(--line)}
.label{font-size:9px;font-weight:500;color:var(--text)}
.field{border:1px solid var(--line);border-radius:3px;font-size:11px;color:var(--ink);display:flex;align-items:center;padding:0 13px;justify-content:space-between}
.field.area{align-items:flex-start;padding-top:10px;color:#8a8f96}

.dropzone{left:366px;top:462px;width:468px;height:128px;border:1.5px dashed var(--drop-line);border-radius:3px;background:var(--drop-bg);text-align:center}
.drop-icon{position:absolute;left:209px;top:16px;width:48px;height:48px;border-radius:50%;background:var(--drop-icon);display:flex;align-items:center;justify-content:center}
.drop-text{position:absolute;left:0;right:0;top:80px;font-size:11px;line-height:16px;color:var(--text)}
.drop-text span{color:var(--link);font-weight:500}

.note-card{left:897px;top:272px;width:214px;height:149px;background:var(--band);border-radius:4px;padding:20px}
.note-card h3{font-size:15.5px;font-weight:500;margin-bottom:10px}
.note-card p{font-size:11.8px;line-height:20.5px;color:var(--text)}

.percent{left:92px;top:664px;font-size:27px;font-weight:700}
.percent small{font-size:13px;font-weight:500}
.progress{left:0;top:702px;width:1200px;height:7px;background:#f1f2f4}
.progress-fill{height:7px;width:937px;background:var(--teal)}
.btn-primary{left:978px;top:723px;width:133px;height:31px;background:var(--brand);border-radius:3px;color:var(--white);font-size:11.5px;font-weight:500;display:flex;align-items:center;justify-content:center}
</style>
</head>
<body>
<div class="canvas">
  <header class="abs topbar"></header>
  <div class="abs brand"><span class="brand-dot"></span>Velvorn</div>
  <span class="abs nav-item active" style="left:487px">Assessments</span>
  <span class="abs nav-item" style="left:587px">Colleagues</span>
  <span class="abs nav-item" style="left:670px">Results</span>
  <div class="abs nav-underline"></div>
  <svg class="abs icon" style="left:1027px" width="18" height="20" viewBox="0 0 18 20" fill="none" stroke="#fff" stroke-width="1.4"><path d="M4 14V8a5 5 0 0110 0v6l1.5 2h-13z"/><path d="M7 18a2 2 0 004 0"/></svg>
  <svg class="abs icon" style="left:1062px" width="19" height="19" viewBox="0 0 20 20" fill="none" stroke="#fff"><circle cx="10" cy="10" r="7.2" stroke-width="3" stroke-dasharray="2.8 2.85"/><circle cx="10" cy="10" r="5.6" stroke-width="1.4"/><circle cx="10" cy="10" r="2.2" stroke-width="1.4"/></svg>
  <div class="abs avatar" role="img" aria-label="User profile photo"></div>

  <nav class="abs crumbs">
    <svg width="20" height="20" viewBox="0 0 20 20" fill="none" stroke="#0e78bb" stroke-width="1.6"><circle cx="10" cy="10" r="9"/><path d="M14 10H6M9.5 6.5L6 10l3.5 3.5"/></svg>
    <a>Assessment</a><span>/</span><span>Application Design Capabilities</span>
  </nav>
  <svg class="abs" style="left:88px;top:101px" width="22" height="22" viewBox="0 0 22 22" fill="none" stroke="#3b4048" stroke-width="1.4"><path d="M13 20H2V2h14v8"/><path d="M5 6h2M9 6h4M5 10h2M9 10h3M5 14h2"/><circle cx="15" cy="15" r="4"/><path d="M13.3 15l1.2 1.2 2-2.2M18 18l2.5 2.5"/></svg>
  <h1 class="abs title">Application Design Capabilities</h1>
  <div class="abs updated">Last Updated: <b>23/05/2024</b></div>

  <div class="abs band"></div>
  <div class="abs meta" style="left:88px">Assessment Date: <span class="val">May 20, 2024</span></div>
  <div class="abs sep" style="left:267px"></div>
  <div class="abs meta" style="left:288px">Assessment Type: <span class="val">UI/UX Skill</span></div>
  <div class="abs sep" style="left:452px"></div>
  <div class="abs meta" style="left:473px">Due Date: <span class="plain">24/05/2024</span></div>
  <div class="abs pill" style="left:889px;width:41px">Quiz</div>
  <div class="abs pill" style="left:937px;width:88px">Endorsement</div>
  <div class="abs pill" style="left:1032px;width:79px">Submission</div>

  <div class="abs step" style="top:219px">Quiz<span class="tick"><svg width="8" height="8" viewBox="0 0 8 8" fill="none" stroke="#fff" stroke-width="1.4"><path d="M1.5 4l1.7 1.7L6.5 2.3"/></svg></span></div>
  <div class="abs step" style="top:271px">Endorsement<span class="tick"><svg width="8" height="8" viewBox="0 0 8 8" fill="none" stroke="#fff" stroke-width="1.4"><path d="M1.5 4l1.7 1.7L6.5 2.3"/></svg></span></div>
  <div class="abs step current" style="top:322px">Submission</div>

  <h2 class="abs section-title">Submission</h2>
  <div class="abs btn-outline" style="left:1008px;top:213px;width:103px;height:31px">Save Progress</div>
  <div class="abs rule"></div>

  <div class="abs label" style="left:366px;top:273px">Document Name</div>
  <div class="abs field" style="left:366px;top:291px;width:224px;height:31px">MyPortfolio_2</div>
  <div class="abs label" style="left:610px;top:273px">Document Category</div>
  <div class="abs field" style="left:610px;top:291px;width:224px;height:31px">Resume<svg width="10" height="6" viewBox="0 0 10 6" fill="none" stroke="#3b4048" stroke-width="1.3"><path d="M1 1l4 4 4-4"/></svg></div>
  <div class="abs label" style="left:366px;top:337px">Note</div>
  <div class="abs field area" style="left:366px;top:355px;width:468px;height:93px">Write here</div>

  <div class="abs dropzone">
    <div class="drop-icon"><svg width="28" height="26" viewBox="0 0 28 26" fill="none" stroke="#1b86cf" stroke-width="2" stroke-linecap="round"><path d="M14 16V2M9 6.5L14 2l5 4.5"/><path d="M4 13v8a3 3 0 003 3h14a3 3 0 003-3v-8"/><path d="M4 18h20"/></svg></div>
    <div class="drop-text">Drag &amp; Drop here for upload<br>or <span>browse</span> file</div>
  </div>

  <aside class="abs note-card">
    <h3>Note</h3>
    <p>Lorem ipsum dolor sit amet, consecteteur adispiscing elit. Lorem ipsum dolor sit amet, consecteteur adispiscing.</p>
  </aside>

  <div class="abs percent">75<small>%</small></div>
  <div class="abs progress"><div class="progress-fill"></div></div>
  <div class="abs btn-outline" style="left:88px;top:723px;width:72px;height:31px">Go Back</div>
  <div class="abs btn-primary">Submit Assessment</div>
</div>
</body>
</html>
```